New Business Card Design for Manufacturing

We are an engineering/manufacturing company that offers Advanced machining/assembly/engineering services, as well as innovative products for the heavy duty engine cooling markets.

We are looking to get a new business card designed that is clean and modern looking, but still fits the wide range of technical/skilled work we do.

- We hope to use this design as the base for other design work in new Presentations, web, and print work.

Industry/Entity Type

Engineering

Contact Information for Business Card

Our preferred color of blue is (RGB) 22/71/159 but can vary slightly from that color. Our content will be our Logo and full company name (Vantrell Forge Works, Inc.), company address, name, job title, phone number with extension, cell number, fax number, website, and email address on the cards.
We'd like the full company name next to the logo, but we are open to other interpretations of that layout.
Preferably, we would like the back side to be clean with just our logo, and the front to contain all of the contact information.

Colors
2f74b4
0355a3
85abd2

Requirements
Must have
• - Logo, company name, needed content - We are open to interpretation beyond that.
• - Standard size business card.
• - Horizontal orientation.
• - Enough space for lengthy names / job titles (for example, a job title could read "Directory of Human Resources" or "V.P. of Governmental Affairs"). We need this to look clean, whether the title be short (CEO) or long (as described above).

```html
<!DOCTYPE html>
<html lang="en">
<head>
<meta charset="utf-8">
<title>Vantrell Forge Works — Business Card</title>
<link href="https://fonts.googleapis.com/css2?family=Oswald:wght@500&family=Work+Sans:wght@400;600;700&display=swap" rel="stylesheet">
<style>
  :root {
    --bg: #161616;
    --card-dark: #1c1c1c;
    --card-light: #303030;
    --blue: #1a56b0;
    --blue-bright: #2f74b4;
    --text: #f2f2f2;
    --silver: #bfbfbf;
  }
  * { margin: 0; padding: 0; box-sizing: border-box; }
  html, body {
    width: 1200px; height: 897px; overflow: hidden;
    background: var(--bg);
    font-family: "Work Sans", Arial, sans-serif;
    color: var(--text);
  }
  .canvas { position: relative; width: 1200px; height: 897px; }
  .card {
    position: absolute; left: 304px; width: 594px; height: 338px;
    border-radius: 18px;
    background: linear-gradient(150deg, var(--card-dark) 0%, #232323 50%, var(--card-light) 100%);
    box-shadow: 0 10px 24px rgba(0,0,0,.55);
  }
  .card--front { top: 92px; }
  .card--back { top: 470px; }

  .brand {
    position: absolute; display: flex; align-items: center; gap: 10px;
    font-weight: 700; letter-spacing: .04em; text-transform: uppercase; white-space: nowrap;
  }
  .brand__mark { display: block; background: currentColor; }
  .card--front .brand {
    top: 40px; left: 0; right: 0; justify-content: center;
    color: var(--blue); font-size: 22px;
  }
  .card--front .brand__mark { width: 16px; height: 16px; }
  .card--back .brand {
    top: 150px; left: 0; right: 0; justify-content: center;
    color: var(--silver); font-size: 26px;
  }
  .card--back .brand__mark { width: 20px; height: 20px; }

  .identity { position: absolute; left: 94px; top: 168px; width: 210px; }
  .identity__name {
    font-family: "Oswald", "Arial Narrow", sans-serif; font-weight: 500;
    font-size: 30px; line-height: 1; letter-spacing: .09em; color: var(--blue);
    text-transform: uppercase; white-space: nowrap;
  }
  .identity__title { margin-top: 10px; font-size: 15.5px; white-space: nowrap; }

  .divider {
    position: absolute; left: 321px; top: 152px; width: 2px; height: 82px;
    background: var(--blue);
  }

  .contacts { position: absolute; left: 350px; top: 145px; list-style: none; }
  .contacts li {
    display: flex; align-items: center; gap: 12px;
    height: 19.2px; font-size: 14px; letter-spacing: .02em;
  }
  .contacts svg { width: 12px; height: 12px; flex: none; fill: var(--blue); }

  .location {
    position: absolute; left: 0; right: 0; top: 296px; text-align: center;
    font-size: 14px; letter-spacing: .03em;
  }
  .location__label { color: var(--blue); font-weight: 600; }

  .website {
    position: absolute; left: 0; right: 0; top: 296px; text-align: center;
    font-size: 16px; letter-spacing: .2em;
  }
  .website__accent { color: var(--blue); }
</style>
</head>
<body>
<main class="canvas">
  <section class="card card--front" aria-label="Business card front">
    <div class="brand"><span class="brand__mark"></span>Vantrell Forge Works, Inc.</div>

    <div class="identity">
      <p class="identity__name">Dorian Halvek</p>
      <p class="identity__title">V.P. of Governmental Affairs</p>
    </div>

    <div class="divider"></div>

    <ul class="contacts">
      <li><svg viewBox="0 0 12 12"><path d="M2.4 0.5 4.3 2.6 3.4 4.1c.8 1.7 2.1 3 3.8 3.8l1.5-.9 2.1 1.9-1 2C5 10.8 1.2 7 .5 1.5z"/></svg>+36 30 555 ext</li>
      <li><svg viewBox="0 0 12 12"><path d="M3 0h6v12H3zM4 1.5v8h4v-8z"/></svg>+36 30 555 0142</li>
      <li><svg viewBox="0 0 12 12"><path d="M3 0h6v3H3zM0 4h12v5h-2v3H2V9H0zM3 8v3h6V8z"/></svg>+36 30 555 0142</li>
      <li><svg viewBox="0 0 12 12"><path d="M0 2h12v1L6 7 0 3zM0 4.2 6 8.2l6-4V10H0z"/></svg>info@vantrellforge.com</li>
      <li><svg viewBox="0 0 12 12"><path d="M6 0a6 6 0 1 0 0 12A6 6 0 0 0 6 0zm0 1c.7.7 1.3 2 1.5 3.5h-3C4.7 3 5.3 1.7 6 1zM1.1 5.5h2.4c0 1 .1 1.8.3 2.5H1.6a5 5 0 0 1-.5-2.5zm.5-1c.4-1.2 1.3-2.2 2.5-2.8-.3.8-.6 1.8-.6 2.8zm2.9 1h3c0 1-.1 1.8-.4 2.5H4.9c-.3-.7-.4-1.5-.4-2.5zm4 0h2.4a5 5 0 0 1-.5 2.5H8.2c.2-.7.3-1.5.3-2.5zm1.9-1H8.5c0-1-.3-2-.6-2.8 1.2.6 2.1 1.6 2.5 2.8zM2.2 9h1.9c.3.8.6 1.4 1 1.9A5 5 0 0 1 2.2 9zm3 0h1.6C6.6 9.7 6.3 10.3 6 10.7 5.7 10.3 5.4 9.7 5.2 9zm2.7 0h1.9a5 5 0 0 1-2.9 1.9c.4-.5.7-1.1 1-1.9z"/></svg>www.vantrellforge.com</li>
    </ul>

    <p class="location"><span class="location__label">Location:</span> 2180 Korvath, Mirel str. 27/B, Hungary</p>
  </section>

  <section class="card card--back" aria-label="Business card back">
    <div class="brand"><span class="brand__mark"></span>Vantrell Forge Works, Inc.</div>
    <p class="website">www.<span class="website__accent">vantrellforge</span>.com</p>
  </section>
</main>
</body>
</html>
```